Business Card Design

We need a business card designed for our new company. Prefer a black card with white logo & writing.

Contact Information for Business Card

Ted Galloway, address: 7-4812 Fernhollow Road, Abbotsford, BC, V3K 8R2, Office Phone: 604-712-3390, Cell: 604-947-2164, Email: ted@resinworkshub.ca

Colors

Designer to choose only greyscale colors for use in the design.

```html
<!DOCTYPE html>
<html lang="en">
<head>
<meta charset="utf-8">
<title>Resinworks Hub – Business Card</title>
<link rel="stylesheet" href="https://fonts.googleapis.com/css2?family=Poppins:wght@300;400;700&display=swap">
<style>
  :root {
    --stage: #1f1f21;
    --card: #2a2a2d;
    --ink: #ffffff;
    --ink-soft: #e4e4e6;
    --emboss: #8a8a8e;
  }
  * { margin: 0; padding: 0; box-sizing: border-box; }
  html, body {
    width: 1200px; height: 711px; overflow: hidden;
    background: var(--stage);
    font-family: "Poppins", sans-serif;
  }
  .stage {
    position: relative; width: 1200px; height: 711px;
    display: flex; justify-content: center; align-items: center; gap: 80px;
  }
  .card {
    position: relative;
    width: 300px; height: 525px;
    background: var(--card);
    border-radius: 18px;
    color: var(--ink);
  }
  /* Front */
  .card--front { display: flex; justify-content: center; align-items: center; }
  .brand {
    display: flex; align-items: center; gap: 10px;
  }
  .brand__mark { width: 14px; height: 14px; background: currentColor; }
  .brand__name {
    font-weight: 700; font-size: 26px; letter-spacing: 1px;
    text-transform: uppercase; line-height: 1;
  }
  .card--front .brand { color: var(--emboss); }

  /* Back */
  .card--back { padding: 62px 0 0; text-align: center; }
  .card--back .brand { justify-content: center; color: var(--ink); }
  .card--back .brand__name { font-size: 22px; }
  .person { margin-top: 230px; }
  .person__name { font-size: 27px; line-height: 1.1; }
  .person__first { font-weight: 700; }
  .person__last { font-weight: 300; }
  .person__role { font-size: 12px; font-weight: 400; color: var(--ink-soft); margin-top: 2px; }
  .address {
    margin-top: 26px; font-size: 12px; font-weight: 300; line-height: 1.45;
    font-style: normal; color: var(--ink-soft);
  }
  .contacts {
    list-style: none; margin: 14px auto 0; width: 190px; text-align: left;
    font-size: 12.5px; font-weight: 300; color: var(--ink-soft);
  }
  .contacts li { display: flex; align-items: center; gap: 9px; line-height: 1.6; }
  .contacts svg { width: 11px; height: 11px; flex: none; fill: none; stroke: var(--ink); stroke-width: 1.6; }
</style>
</head>
<body>
<main class="stage">
  <section class="card card--front" aria-label="Card front">
    <div class="brand">
      <span class="brand__mark"></span>
      <span class="brand__name">Resinworks Hub</span>
    </div>
  </section>

  <section class="card card--back" aria-label="Card back">
    <div class="brand">
      <span class="brand__mark"></span>
      <span class="brand__name">Resinworks Hub</span>
    </div>

    <div class="person">
      <h1 class="person__name"><span class="person__first">Ted</span> <span class="person__last">Galloway</span></h1>
      <p class="person__role">Founder &amp; CEO</p>
    </div>

    <address class="address">7-4812 Fernhollow Road,<br>Abbotsford, BC, V3K 8R2.</address>

    <ul class="contacts">
      <li>
        <svg viewBox="0 0 12 12"><path d="M3 1.5 L4.5 4 L3.5 5 Q5 7.5 7 8.5 L8 7.5 L10.5 9 L9.5 10.8 Q4 10 1.2 3 Z"/></svg>
        604-712-3390
      </li>
      <li>
        <svg viewBox="0 0 12 12"><rect x="3" y="1" width="6" height="10" rx="1"/><path d="M5.5 9h1"/></svg>
        604-947-2164
      </li>
      <li>
        <svg viewBox="0 0 12 12"><circle cx="6" cy="6" r="4.8"/><path d="M1.2 6h9.6M6 1.2q-2.5 4.8 0 9.6M6 1.2q2.5 4.8 0 9.6"/></svg>
        www.resinworkshub.ca
      </li>
      <li>
        <svg viewBox="0 0 12 12"><rect x="1" y="2.5" width="10" height="7" rx="0.8"/><path d="M1 3l5 3.5 5-3.5"/></svg>
        ted@resinworkshub.ca
      </li>
    </ul>
  </section>
</main>
</body>
</html>
```